BUSINESS CARD DESIGN

NAME- DALE VORSKIN
PHONE NUMER - 555- 714-9082
EMAIL- OFFICE@TRV-GROUNDMAKRZ.COM
BACK OF CARD- SPEACIALIZES IN LAND CLEARING, FORESTRY MUCLHING AND EXCAVATION

Contact Information for Business Card

NAME- DALE VORSKIN PHONE NUMER - 555- 714-9082 EMAIL- OFFICE@TRV-GROUNDMAKRZ.COM BACK OF CARD- SPEACIALIZES IN LAND CLEARING , MUCLHING AND EXCAVATION

```html
<!DOCTYPE html>
<html lang="en">
<head>
<meta charset="utf-8">
<title>Traverse Groundmakrz – Business Card</title>
<link href="https://fonts.googleapis.com/css2?family=Montserrat:wght@700;800&display=swap" rel="stylesheet">
<style>
  :root {
    --gold: #fdb515;
    --ink: #000000;
    --paper: #ffffff;
    --page: #ffffff;
    --edge: #e2e2e2;
    --shade: rgba(0, 0, 0, 0.35);
  }
  html, body { margin: 0; padding: 0; overflow: hidden; }
  body {
    width: 1200px; height: 1132px; background: var(--page);
    position: relative; font-family: "Montserrat", sans-serif;
  }
  .card {
    position: absolute; left: 255px; width: 690px; height: 394px;
    overflow: hidden; box-sizing: border-box;
    box-shadow: 10px 14px 22px var(--shade);
  }
  .card--front { top: 151px; background: var(--paper); border: 1px solid var(--edge); }
  .card--back { top: 627px; background: var(--ink); }
  .front-panel { position: absolute; left: -1px; top: -1px; width: 690px; height: 394px; }
  .brand {
    position: absolute; display: flex; flex-direction: column; align-items: center;
    color: var(--gold); font-weight: 800; text-align: center;
  }
  .brand-mark { border-radius: 50%; background: var(--gold); }
  .brand-name { letter-spacing: 2px; line-height: 1.25; margin-top: 14px; white-space: nowrap; }
  .card--front .brand { left: 43px; width: 210px; top: 99px; }
  .card--front .brand-mark { width: 110px; height: 110px; }
  .card--front .brand-name { font-size: 15px; }
  .card--back .brand { left: 195px; width: 300px; top: 75px; }
  .card--back .brand-mark { width: 150px; height: 150px; }
  .card--back .brand-name { font-size: 20px; margin-top: 18px; }
  .holder { position: absolute; left: 372px; top: 83px; color: var(--gold); font-weight: 700; }
  .holder-name { font-size: 31px; line-height: 1; margin: 0; white-space: nowrap; }
  .holder-role {
    font-size: 22px; line-height: 1; margin: 8px 0 0; padding-bottom: 4px;
    width: 101px; border-bottom: 3px solid var(--ink);
  }
  .contacts { position: absolute; left: 372px; top: 209px; margin: 0; padding: 0; list-style: none; }
  .contact { display: flex; align-items: center; height: 26px; margin-bottom: 15px; }
  .contact svg { width: 26px; height: 26px; margin-right: 17px; flex: none; }
  .contact span { color: var(--gold); font-weight: 700; font-size: 14px; white-space: nowrap; }
  .tagline {
    position: absolute; left: 0; right: 0; top: 345px; margin: 0; text-align: center;
    color: var(--gold); font-weight: 700; font-size: 13.5px; letter-spacing: 1.1px; white-space: nowrap;
  }
</style>
</head>
<body>
  <section class="card card--front">
    <svg class="front-panel" viewBox="0 0 690 394" aria-hidden="true">
      <polygon points="0,0 218,0 381,394 0,394" fill="var(--ink)"/>
    </svg>
    <div class="brand">
      <div class="brand-mark"></div>
      <div class="brand-name">TRAVERSE<br>GROUNDMAKRZ LLC<br>555-714-9082</div>
    </div>
    <div class="holder">
      <p class="holder-name">DALE VORSKIN</p>
      <p class="holder-role">OWNER</p>
    </div>
    <ul class="contacts">
      <li class="contact">
        <svg viewBox="0 0 26 26" fill="none" stroke="var(--ink)" stroke-width="2"><rect x="2" y="6" width="22" height="15"/><path d="M2 6l11 9 11-9M2 21l8-8M24 21l-8-8"/></svg>
        <span>OFFICE@TRV-GROUNDMAKRZ.COM</span>
      </li>
      <li class="contact">
        <svg viewBox="0 0 26 26" fill="none" stroke="var(--ink)" stroke-width="1.8"><path d="M6 3l4 5-2 3c1 3 4 6 7 7l3-2 5 4-3 4C12 23 3 14 2 6z"/><path d="M15 6a6 6 0 0 1 5 5M15 2a10 10 0 0 1 9 9"/></svg>
        <span>+555- 714-9082</span>
      </li>
      <li class="contact">
        <svg viewBox="0 0 26 26" fill="none" stroke="var(--ink)" stroke-width="1.6"><circle cx="13" cy="13" r="11"/><ellipse cx="13" cy="13" rx="5" ry="11"/><path d="M2 13h22M4 7h18M4 19h18"/></svg>
        <span>WWW.TRV-GROUNDMAKRZ.COM</span>
      </li>
    </ul>
  </section>

  <section class="card card--back">
    <div class="brand">
      <div class="brand-mark"></div>
      <div class="brand-name">TRAVERSE<br>GROUNDMAKRZ LLC<br>555-714-9082</div>
    </div>
    <p class="tagline">SPEACIALIZES IN LAND CLEARING , MUCLHING AND EXCAVATION</p>
  </section>
</body>
</html>
```